Webdesign für Full-Service-Internetagentur
Zielgruppe
Falkenhainer Webdesign – Ihr Partner für außergewöhnliche Onlinepräsenzen
Wir bieten seit mehr als 16 Jahren Internetauftritte für kleine und mittelständische Unternehmen an.
Als Full-Service-Internetagentur liefern wir Ihnen individuelle auf Ihre Bedürfnisse, Ihre Branche und Ihre Zielgruppe zugeschnittene Lösungen für Ihre Onlinepräsentation an. Unser Angebot beinhaltet sowohl ein ideenreiches Webdesign kombiniert mit den aktuellsten Grundsätzen für Web-Programmierung als auch die Unterstützung für Ihr erfolgreiches Werben im Internet.
Eine gute Beratung heißt für uns genau hinhören und verstehen, was Sie wirklich brauchen. Je besser wir Ihre Ziele kennen, desto besser können wir Ihre Onlinepräsenz umsetzen. Unsere Kundenberater erläutern Ihnen persönlich mit Enthusiasmus die verschiedenen Möglichkeiten der Darstellung Ihrer Firma im Internet und entwickeln Konzepte, die Ihren Anforderungen bestmöglich entsprechen. Nicht nur während der Projektphase, sondern auch nach Onlinestellung Ihrer Internetseite stehen wir Ihnen mit persönlicher Kundenbetreuung und Supportdienstleistungen zur Verfügung.
Aufgabenstellung
siehe : https://www.falkenhainer-webdesign.example/

```html
<!DOCTYPE html>
<html lang="de">
<head>
<meta charset="utf-8">
<title>Falkenhainer Webdesign – Webseiten mit Weitblick</title>
<link href="https://fonts.googleapis.com/css2?family=Poppins:ital,wght@0,300;0,400;0,500;0,600;0,700;1,400&display=swap" rel="stylesheet">
<style>
:root{
  --red:#e3262b;
  --ink:#1c1c1c;
  --text:#555;
  --muted:#a9a9a9;
  --line:#e2e2e2;
  --pale:#fbf3f3;
  --white:#fff;
}
*{box-sizing:border-box;margin:0;padding:0}
html,body{width:1200px;height:3824px;overflow:hidden;background:var(--white)}
body{position:relative;font-family:"Poppins",sans-serif;color:var(--text)}
.abs{position:absolute}
.red{color:var(--red)}
.eyebrow{font-size:9px;font-weight:600;letter-spacing:.5px;text-transform:uppercase;color:var(--muted)}
.eyebrow.red{color:var(--red)}
.h2{font-size:25px;font-weight:600;color:var(--ink);line-height:35px}
.rule{width:30px;height:2px;background:var(--red)}
.photo{position:absolute}

/* header */
.logo{left:235px;top:46px;font-size:20px;color:var(--ink);font-weight:500;letter-spacing:-.3px;display:flex;align-items:center;gap:8px}
.logo i{display:block;width:10px;height:10px;background:var(--red)}
.tagline{left:253px;top:73px;font-size:8px;color:var(--ink)}
.nav{left:547px;top:53px;display:flex;gap:26px;font-size:11.5px;font-weight:500;color:var(--ink)}
.nav .active{color:var(--red)}
.top-phone{left:848px;top:22px;font-size:12px;color:var(--red);display:flex;align-items:center;gap:6px}
.badge{left:1100px;top:9px;width:76px;height:98px;background:#8c1f22;border:2px solid #ddd;border-radius:3px}

/* hero */
.hero-mark{left:58px;top:264px;width:2px;height:34px;background:var(--red)}
.hero-title{left:233px;top:266px;font-size:39px;font-weight:700;color:var(--ink);line-height:48px}
.hero-sub{left:233px;top:369px;font-size:12.5px;color:var(--ink)}
.btn{background:var(--red);color:#fff;font-size:9px;font-weight:600;letter-spacing:.5px;display:flex;align-items:center;justify-content:center;gap:8px}
.hero-btn{left:236px;top:411px;width:115px;height:30px}

/* intro */
.intro-bg{left:0;top:638px;width:1200px;height:510px;background:linear-gradient(#fff,var(--pale) 60%,#f8e4e4)}
.ghost{font-weight:700;color:rgba(0,0,0,.035);line-height:1}
.intro-title{left:233px;top:648px;font-size:23px;font-weight:500;color:var(--ink);line-height:35px}
.intro-text{left:609px;top:644px;width:352px;font-size:10.5px;line-height:21.5px;color:#777}
.intro-text p+p{margin-top:7px}
.card{background:#fff;height:218px;width:232px;top:854px;text-align:center;padding:56px 16px 0}
.card h3{font-size:12.5px;font-weight:600;color:var(--ink);margin:12px 0 6px}
.card p{font-size:10.5px;line-height:19px;color:var(--muted)}
.card svg{width:48px;height:48px}

/* about */
.about-text{left:606px;top:1258px;width:360px}
.about-text .h2{margin-top:8px}
.about-text p{font-size:10.5px;line-height:21.5px;color:#777;margin-top:18px}
.about-text .more{font-size:11px;color:var(--red);font-weight:500;margin-top:12px;display:block}

/* references */
.ref-head{left:233px;top:1663px}
.ref-head .h2{margin-top:8px}
.ref-btn{left:840px;top:1734px;width:126px;height:31px;border:1px solid var(--line);font-size:9px;font-weight:600;color:var(--ink);display:flex;align-items:center;justify-content:center}
.shot{top:1835px;width:270px;height:271px;border:1px solid var(--line)}

/* testimonial */
.quote{left:235px;top:2205px;width:380px}
.quote .h2{margin-top:10px}
.quote h4{font-size:10.5px;font-weight:600;color:var(--ink);margin-top:46px}
.quote p{font-size:10px;line-height:15px;color:#666;margin-top:4px}
.quote p.italic{font-style:italic;margin-top:12px}
.quote-logo{left:235px;top:2488px;display:flex;align-items:center;gap:8px;font-size:8.5px;font-weight:600;color:var(--ink);line-height:10px}
.dots{left:577px;top:2502px;display:flex;gap:6px}
.dots i{width:5px;height:5px;border-radius:50%;background:var(--line)}
.dots i:first-child{background:var(--red)}

/* clients */
.clients{left:30px;top:2658px;width:1140px;height:52px;display:flex;justify-content:space-between;align-items:center;font-size:20px;font-weight:700;color:#444}
.clients span{display:flex;align-items:center;gap:8px}
.clients i{display:inline-block;width:12px;height:12px;background:var(--red)}

/* process */
.process{left:0;top:2737px;width:1200px;height:481px;background:var(--red);overflow:hidden}
.process .ghost{position:absolute;left:140px;top:-42px;font-size:110px;color:rgba(255,255,255,.12);white-space:nowrap}
.process-head{position:absolute;left:0;top:89px;width:1200px;text-align:center;color:#fff}
.process-head .eyebrow{color:#fff;opacity:.85}
.process-head h2{font-size:25px;font-weight:600;line-height:34px;margin-top:6px}
.process-head .rule{background:#fff;margin:10px auto 0}
.step{position:absolute;top:215px;width:200px;height:199px;text-align:center;color:#fff;padding-top:26px}
.step.on{background:#fff;color:var(--red)}
.step h3{font-size:12.5px;font-weight:500;margin:10px 0 12px}
.step p{font-size:10px;line-height:19px;padding:0 18px}
.step.on p{color:var(--muted)}
.step svg{width:46px;height:46px}

/* contact */
.form-title{left:235px;top:3252px;font-size:19px;font-weight:600;color:var(--ink)}
.field{height:32px;border:1px solid var(--line);font-size:8.5px;color:#999;padding:10px 11px}
.check{left:236px;top:3515px;width:17px;height:17px;border:1px solid #ccc}
.consent{left:268px;top:3510px;width:335px;font-size:8.3px;line-height:13.5px;color:var(--ink)}
.send{left:241px;top:3590px;width:124px;height:27px;border-radius:14px}
.contact-side{left:674px;top:3257px;width:330px}
.contact-side h2{font-size:21px;font-weight:600;color:var(--ink);line-height:35px;margin-top:8px}
.contact-side .rule{margin-top:8px}
.contact-side p{font-size:11px;color:#999;line-height:15px;margin-top:22px}
.contact-side strong{display:block;font-size:17px;color:var(--ink);font-weight:500;margin-top:6px}

/* footer */
.foot-h{font-size:10px;font-weight:500;color:var(--red);text-transform:uppercase}
.foot-list{font-size:9.5px;line-height:19px;color:var(--ink)}
.copy{left:235px;top:3781px;font-size:9px;color:var(--ink)}
</style>
</head>
<body>

<!-- Header -->
<div class="abs logo"><i></i>Falkenhainer Webdesign</div>
<div class="abs tagline">Webseiten mit Weitblick</div>
<nav class="abs nav"><span class="active">Die Agentur</span><span>Referenzen</span><span>Engagement</span><span>Aktuelles</span><span>Kontakt</span><span>FAQ</span></nav>
<div class="abs top-phone">
  <svg width="18" height="16" viewBox="0 0 24 24" fill="none" stroke="currentColor" stroke-width="2"><path d="M5 3h4l2 5-3 2a12 12 0 0 0 6 6l2-3 5 2v4a2 2 0 0 1-2 2A17 17 0 0 1 3 5a2 2 0 0 1 2-2z"/></svg>
  0341 - 5550120
</div>
<div class="abs badge" role="img" aria-label="Partnersiegel"></div>

<!-- Hero -->
<div class="abs hero-mark"></div>
<div class="photo" role="img" aria-label="Foto: Team arbeitet gemeinsam an einem Entwurf" style="left:500px;top:110px;width:680px;height:450px;background:radial-gradient(ellipse at 55% 50%,#7b6a5e 0%,#a89384 45%,#d8cdc4 70%,rgba(255,255,255,0) 74%)"></div>
<h1 class="abs hero-title">Lasst uns beginnen<br>Zusammenarbeiten</h1>
<p class="abs hero-sub">Wir bieten Ihnen alle Arten von Online-Diensten</p>
<div class="abs btn hero-btn">WEITERLESEN
  <svg width="12" height="8" viewBox="0 0 12 8" fill="none" stroke="#fff" stroke-width="1.2"><path d="M0 4h11M8 1l3 3-3 3"/></svg></div>

<!-- Intro -->
<div class="abs intro-bg"></div>
<div class="abs ghost" style="left:30px;top:640px;font-size:170px">W</div>
<h2 class="abs intro-title">Wir sind dynamisch<br>Team von kreativen Menschen<br>der Innovation<br>&amp; Entwicklungskompetenz.</h2>
<div class="abs intro-text">
  <p>Wir bieten Web- und Entwicklungsservices für Startups und kleine Unternehmen, um einen Partner für Ihre Anforderungen in den Bereichen digitale Medien, Designentwicklung, Lead-Generierung und Kommunikation zu suchen. Wir arbeiten mit Ihnen, nicht für Sie. Obwohl wir große Ressourcen haben.</p>
  <p>Wir haben unseren Hauptsitz in Deutschland, um einen Kunden bestmöglich bedienen zu können Basis, die sich weltweit erstreckt.</p>
</div>

<div class="abs card" style="left:108px">
  <svg viewBox="0 0 48 48" fill="none" stroke="var(--red)" stroke-width="1.6"><rect x="6" y="10" width="10" height="32"/><path d="M6 16h4M6 22h4M6 28h4M6 34h4"/><path d="M22 42V14l4-6 4 6v28z"/><rect x="34" y="8" width="8" height="34"/></svg>
  <h3>Konzeption &amp; Beratung</h3>
  <p>Wir entwickeln Ihr individuelles Konzept und begleiten Sie über die Fertigstellung hinaus.</p>
</div>
<div class="abs card" style="left:359px">
  <svg viewBox="0 0 48 48" fill="none" stroke="var(--red)" stroke-width="1.6"><rect x="14" y="6" width="30" height="22"/><path d="M24 34h10M29 28v6"/><rect x="4" y="18" width="12" height="22"/><path d="M26 20l8-8M30 12h4v4"/></svg>
  <h3>Webdesign &amp; Programmierung</h3>
  <p>Wir setzen Ihre individuell gestaltete Webseite mittels aktueller Web-Technologien um.</p>
</div>
<div class="abs card" style="left:609px">
  <svg viewBox="0 0 48 48" fill="none" stroke="var(--red)" stroke-width="1.6"><circle cx="24" cy="24" r="20"/><path d="M12 30l8-8 6 5 10-11M30 16h6v6"/></svg>
  <h3>SEO &amp; Online Marketing</h3>
  <p>Wir analysieren Ihre Webseite und schaffen Voraussetzungen für ein optimales Suchmaschinen-Ranking.</p>
</div>
<div class="abs card" style="left:857px">
  <svg viewBox="0 0 48 48" fill="none" stroke="var(--red)" stroke-width="1.6"><rect x="6" y="6" width="36" height="36"/><path d="M6 13h36"/><text x="24" y="33" text-anchor="middle" font-family="Poppins,sans-serif" font-size="12" font-weight="600" fill="var(--red)" stroke="none">.de</text></svg>
  <h3>Domain &amp; Webhosting</h3>
  <p>Alles was Sie für Ihr Webprojekt brauchen.</p>
</div>

<!-- About -->
<div class="abs ghost" style="left:520px;top:1245px;font-size:150px">E</div>
<div class="photo" role="img" aria-label="Foto: Kollegen arbeiten gemeinsam am Computer" style="left:30px;top:1232px;width:535px;height:342px;background:radial-gradient(ellipse at 50% 50%,#4d4540 0%,#8a7a70 45%,#d3c9c2 68%,rgba(255,255,255,0) 72%)"></div>
<div class="abs about-text">
  <div class="eyebrow">Ehrlich. Stressgeprobt. Verständlich. Erfolgreich.</div>
  <h2 class="h2">Erfrischendes und kreatives<br>Webdesign</h2>
  <p>Unsere Leistungen sind transparent und die Projektkosten sind realistisch. Wir versprechen nicht zu viel und verschweigen auch nicht potentielle Ecken und Kanten. Online wie offline ist vieles möglich, aber längst nicht alles ist sinnvoll.</p>
  <p>Profitieren Sie von unseren aufeinander abgestimmten Dienstleistungen, und lassen Sie Ihr Projekt gemeinsam erfolgreich umsetzen. Am besten vereinbaren Sie gleich unter <span class="red">0341 5550120</span> oder <span class="red" style="text-decoration:underline">info@falkenhainer-webdesign.example</span> einen Termin, der bei uns in Falkenhain oder vor Ort bei Ihnen stattfinden kann.</p>
  <span class="more">Weiterlesen →</span>
</div>

<!-- References -->
<div class="abs ghost" style="left:70px;top:1640px;font-size:160px">K</div>
<div class="abs ref-head">
  <div class="eyebrow red">References</div>
  <h2 class="h2">Wir haben viel Arbeit geleistet Überprüfen<br>Sie einige von hier</h2>
  <div class="rule" style="margin-top:14px"></div>
</div>
<div class="abs ref-btn">SIEHE ALLE PROJEKTE</div>
<div class="abs shot" role="img" aria-label="Referenz: Webseite eines Vereins" style="left:27px;background:linear-gradient(#fff 0,#fff 8%,#e9b46a 8%,#f3d6a0 50%,#fff 50%,#fff 94%,#2f8fd8 94%)"></div>
<div class="abs shot" role="img" aria-label="Referenz: Webseite eines Bauunternehmens" style="left:319px;background:linear-gradient(#9b2a2a 0,#9b2a2a 9%,#b7b2ac 9%,#d7d3ce 48%,#fff 48%,#fff 62%,#8a8376 62%)"></div>
<div class="abs shot" role="img" aria-label="Referenz: Webseite eines Malerbetriebs" style="left:613px;background:linear-gradient(#fff 0,#fff 6%,#eef1f5 6%,#d5dbe4 42%,#fff 42%)"></div>
<div class="abs shot" role="img" aria-label="Referenz: Webseite eines Wohnmobilhändlers" style="left:906px;background:linear-gradient(#fff 0,#fff 9%,#7fb1dc 9%,#c7dbe9 48%,#fff 48%,#fff 70%,#ececec 70%)"></div>

<!-- Testimonial -->
<div class="photo" role="img" aria-label="Foto: Paar schaut lächelnd auf ein Tablet" style="left:639px;top:2198px;width:549px;height:386px;background:radial-gradient(ellipse at 55% 50%,#6b4a3e 0%,#b48c78 40%,#e3d4ca 66%,rgba(255,255,255,0) 70%)"></div>
<div class="abs quote">
  <div class="eyebrow">Kundenfeedback</div>
  <h2 class="h2">Unser Kunde liebt uns, weil<br>unserer Qualitätsarbeit.</h2>
  <div class="rule" style="margin-top:14px"></div>
  <h4>Fachverband Oberflächen &amp; Bautenschutz Mitte</h4>
  <p>Erneute Widerwahl als Vorstandsmitglied im Bereich PR, Öffentlichkeitsarbeit bei Fachverband Mitte Oberflächen, Gestaltung, Bautenschutz in Dresden</p>
  <p class="italic">Der Fachverband ist mehr als nur ein starkes Trio – unser gemeinsames Ziel sind die Organisation, die Partnerschaften und die Perspektiven.</p>
</div>
<div class="abs quote-logo"><i style="display:block;width:14px;height:14px;background:var(--red)"></i><span>Fachverband<br>Oberflächen &amp; Bautenschutz<br>Mitte</span></div>
<div class="abs dots"><i></i><i></i><i></i></div>

<!-- Clients -->
<div class="abs clients">
  <span>Holzwerk Brandt</span>
  <span>Kessler</span>
  <span>Rovatec</span>
  <span>Reisedienst Malow</span>
  <span>Novena</span>
  <span><i></i>Telmar</span>
  <span>Vexa</span>
</div>

<!-- Process -->
<section class="abs process">
  <div class="ghost">wird bearbeitet</div>
  <div class="process-head">
    <div class="eyebrow">Wird bearbeitet</div>
    <h2>Wir schließen jedes Projekt mit ab<br>Hand erleben</h2>
    <div class="rule"></div>
  </div>
  <div class="step on" style="left:235px">
    <svg viewBox="0 0 48 48" fill="none" stroke="var(--red)" stroke-width="1.6"><path d="M24 12a10 10 0 0 0-6 18v4h12v-4a10 10 0 0 0-6-18zM19 38h10M21 42h6M24 2v5M8 10l4 3M40 10l-4 3M4 24h5M39 24h5"/></svg>
    <h3>Idee</h3>
    <p>Unser erster Schritt ist die Suche nach einer Idee basierend auf Kundeninformationen</p>
  </div>
  <div class="step" style="left:500px">
    <svg viewBox="0 0 48 48" fill="none" stroke="#fff" stroke-width="1.6"><path d="M14 10h20l8 10-18 20L6 20zM6 20h36M18 10l-4 10 10 20 10-20-4-10"/></svg>
    <h3>Wireframing</h3>
    <p>Auf die Ideen kommen wir alle Ideen in Skizze zum Start</p>
  </div>
  <div class="step" style="left:766px">
    <svg viewBox="0 0 48 48" fill="none" stroke="#fff" stroke-width="1.6"><path d="M40 8c-10 0-18 6-22 16l6 6c10-4 16-12 16-22zM18 24l-8 2-4 6 8-1M24 30l-2 8-6 4 1-8"/><circle cx="31" cy="17" r="3"/></svg>
    <h3>Entwicklung</h3>
    <p>Nach Abschluss der Skizze sind wir werde es vervollständigen</p>
  </div>
</section>

<!-- Contact -->
<h2 class="abs form-title">Wir haben Ihr Interesse geweckt?</h2>
<div class="abs field" style="left:235px;top:3296px;width:176px">Name *</div>
<div class="abs field" style="left:423px;top:3296px;width:175px">Firma</div>
<div class="abs field" style="left:235px;top:3334px;width:176px">Straße, Nr.</div>
<div class="abs field" style="left:423px;top:3334px;width:175px">PLZ, Ort</div>
<div class="abs field" style="left:235px;top:3372px;width:176px">Telefon *</div>
<div class="abs field" style="left:423px;top:3372px;width:175px">E-Mail *</div>
<div class="abs field" style="left:235px;top:3410px;width:363px;height:80px">Ihre Nachricht an uns *</div>
<div class="abs check"></div>
<p class="abs consent">Ich habe die Datenschutzerklärung zur Kenntnis genommen. Ich stimme zu, dass meine Angaben und Daten zur Beantwortung meiner Anfrage elektronisch erhoben und gespeichert werden. Hinweis: Sie können Ihre Einwilligung jederzeit für die Zukunft per E-Mail an <span class="red">info@falkenhainer-webdesign.example</span> widerrufen.</p>
<div class="abs btn send">FORMULAR ABSCHICKEN</div>

<div class="abs contact-side">
  <div class="eyebrow">Kontaktiere uns</div>
  <h2>Zögern Sie nicht<br>Kontaktieren Sie uns für alle<br>Art von Informationen</h2>
  <div class="rule"></div>
  <p>Rufen Sie uns zur sofortigen Unterstützung diese Nummer an</p>
  <strong>0341 - 5550120</strong>
</div>

<!-- Footer -->
<div class="abs foot-h" style="left:235px;top:3660px">Navigation</div>
<div class="abs foot-list" style="left:235px;top:3678px">Portfolio<br>Die Agentur<br>Referenzen<br>Aktuelles</div>
<div class="abs foot-list" style="left:319px;top:3678px">Kontakt<br>FAQ<br>Impressum<br>Datenschutz</div>
<div class="abs foot-h" style="left:466px;top:3660px">Kontakt</div>
<div class="abs foot-list" style="left:466px;top:3678px;line-height:14px">Falkenhainer Webdesign<br>Inh. Lena Hartmann<br>Lindenweg 14<br>09999 Falkenhain</div>
<div class="abs foot-list" style="left:654px;top:3678px;line-height:14px">Fon: 0341 - 5550120<br>Fax: 0341 - 5550121<br><span class="red">info@falkenhainer-webdesign.example</span></div>
<div class="abs copy">© 2019 by <span class="red">Falkenhainer Webdesign</span></div>

</body>
</html>
```